Kor'v Meridell Travel

We need a sleek, professional, inviting card to elicit global travel for the experienced and professional traveler. Royal blue, black and silver. (perhaps the wording could be silver with black shadow?-get creative) Maybe a watermark on the front and the full raised logo on the back.
We want a stylish and modern card, but professional.

```html
<!DOCTYPE html>
<html lang="en">
<head>
<meta charset="utf-8">
<title>Kor'v Meridell Travel — Business Card</title>
<link rel="stylesheet" href="https://fonts.googleapis.com/css2?family=Roboto:wght@400;500;700&display=swap">
<style>
  :root {
    --sky-blue: #29a6de;
    --sky-blue-deep: #1f93c9;
    --card-white: #ffffff;
    --accent-green: #7cc242;
    --backdrop: #3a3c3f;
    --text-light: #ffffff;
  }
  * { box-sizing: border-box; margin: 0; padding: 0; }
  html, body {
    width: 1200px; height: 960px; overflow: hidden;
    background: var(--backdrop);
    font-family: "Roboto", Arial, sans-serif;
  }
  .canvas {
    width: 1200px; height: 960px;
    display: flex; flex-direction: column;
    align-items: center; justify-content: center; gap: 50px;
  }
  .card {
    position: relative;
    width: 700px; height: 400px;
    overflow: hidden;
    box-shadow: 0 10px 30px rgba(0,0,0,0.45);
  }
  /* Front */
  .card-front {
    background: var(--sky-blue);
    display: flex; align-items: center; justify-content: center;
  }
  .front-pattern-area {
    position: absolute; inset: 0;
    background: linear-gradient(135deg, var(--sky-blue) 0%, var(--sky-blue-deep) 100%);
  }
  .brand-name {
    position: relative;
    font-weight: 700;
    letter-spacing: 1px;
    text-transform: uppercase;
    line-height: 1;
  }
  .card-front .brand-name {
    color: var(--text-light);
    font-size: 38px;
  }
  /* Back */
  .card-back { background: var(--sky-blue); }
  .card-back .shape-layer { position: absolute; inset: 0; }
  .back-brand {
    position: absolute;
    left: 420px; right: 0; top: 0; height: 400px;
    display: flex; align-items: center; justify-content: center;
    padding-left: 40px;
  }
  .card-back .brand-name {
    color: var(--sky-blue);
    font-size: 24px;
    text-align: center;
  }
  .holder {
    position: absolute; left: 50px; top: 70px;
    color: var(--text-light);
  }
  .holder-name { font-size: 22px; font-weight: 700; }
  .holder-title { font-size: 15px; margin-top: 6px; }
  .contact {
    position: absolute; left: 50px; top: 215px;
    color: var(--text-light);
    font-size: 18px; line-height: 1.25;
  }
  .address-label { font-weight: 700; }
  .contact-list { list-style: none; margin-top: 14px; }
  .contact-list li { display: flex; align-items: center; gap: 10px; }
  .contact-list svg { width: 14px; height: 14px; fill: var(--text-light); flex: none; }
</style>
</head>
<body>
<main class="canvas">
  <section class="card card-front" aria-label="Card front">
    <div class="front-pattern-area" role="img" aria-label="Faint repeating airplane pattern on blue"></div>
    <span class="brand-name">Kor'v Meridell Travel</span>
  </section>

  <section class="card card-back" aria-label="Card back">
    <svg class="shape-layer" viewBox="0 0 700 400" width="700" height="400" aria-hidden="true">
      <path d="M455 0 C370 90 370 300 500 400 L700 400 L700 0 Z" fill="var(--card-white)"/>
      <path d="M440 0 C352 90 352 280 455 375" fill="none" stroke="var(--accent-green)" stroke-width="6"/>
    </svg>
    <div class="back-brand">
      <span class="brand-name">Kor'v Meridell Travel</span>
    </div>
    <div class="holder">
      <p class="holder-name">Dalen Voskar</p>
      <p class="holder-title">Founder &amp; CEO</p>
    </div>
    <div class="contact">
      <p class="address-label">Address:</p>
      <p>47 Harbor Crest Lane</p>
      <p>Suite #B, Marlow, NC 28390</p>
      <ul class="contact-list">
        <li><svg viewBox="0 0 24 24"><path d="M6.6 10.8a15.2 15.2 0 0 0 6.6 6.6l2.2-2.2c.3-.3.7-.4 1-.2 1.1.4 2.3.6 3.6.6.6 0 1 .4 1 1V20c0 .6-.4 1-1 1A17 17 0 0 1 3 4c0-.6.4-1 1-1h3.5c.6 0 1 .4 1 1 0 1.3.2 2.5.6 3.6.1.3 0 .7-.2 1z"/></svg>910-555-0147</li>
        <li><svg viewBox="0 0 24 24"><path d="M2 5h20v14H2z M2 5l10 8 10-8" stroke="#29a6de" stroke-width="1.5"/></svg>info@korvmeridell.com</li>
        <li><svg viewBox="0 0 24 24"><circle cx="12" cy="12" r="10"/><path d="M2 12h20M12 2c3 3 3 17 0 20M12 2c-3 3-3 17 0 20" fill="none" stroke="#29a6de" stroke-width="1.5"/></svg>www.korvmeridell.com</li>
      </ul>
    </div>
  </section>
</main>
</body>
</html>
```